Bright Step Path Flyer, eyecatching

Hi,
To give you an idea of the business for design purposes, #BrighttStepPath is predominantly a recruitment and people development business, ran by me dedicated to training & assisting others in achieving extra income (pt or f/t) around their current commitments, people also have the opportunity to build their own business brand with my support. My brand colours are Red, White and Black, and I would like to incorporate the following text;

#BrightStepPath

Recruiting now! Start today & start earning!

Would you like an extra income, for…
A holiday?…A new car?…Lifestyle changes?
(Can you put a tick box or something similar adjacent to each)

Are you facing…
Redundancy? Birth of a new child? Hefty bills?

If so, I have the solution.

Contact Yvonne Darcott today: (can you insert the appropriate icon for each of the contact details)
Tel: 07419 604172
Twitter: @Bright_StepPath
Email: Yvonne@brightsteppath-example.co.uk
Facebook: www.facebook-example.com/yvonbrightsteppath

Target Market(s)

Women aged 25-45 years, possibly busy mums too, wanting to earn additinal income to allow them more choices, be it family time, money, new challenge, meeting new people, personal development

Industry/Entity Type

Health And Wellness

Font styles to use
Serif
Sans Serif
Decorative
Script

Colors
ec1f27
ffffff
000000

Requirements
Must have
• My heels logo, be clear concise and eye catching, I also have the following strap line if you wish to use;
• Empowering other to achieve
• Also I have attached a closeup picture of myself but would ideally only like half my face to appear (leftside) similar to the other picture posted - if you can
Nice to have
• Perhaps adding other forms of graphics, or the 3rd picture I have attached with myself...possibly just the shoes though
Should not have
• Too many colours

```html
<!DOCTYPE html>
<html lang="en">
<head>
<meta charset="utf-8">
<title>Bright Step Path – Recruiting Flyer</title>
<link rel="stylesheet" href="https://fonts.googleapis.com/css2?family=Oswald:wght@300;400;500;600&family=Open+Sans:wght@400;600;700&display=swap">
<style>
  :root{
    --red:#ec1f27;
    --white:#ffffff;
    --black:#000000;
    --ink:#1a1a1a;
    --frame:#eeeeee;
    --grey:#9a9a9a;
    --photo-light:#ededed;
    --photo-pale:#c9c9c9;
    --photo-mid:#4a4a4a;
    --photo-dark:#111111;
  }
  *{box-sizing:border-box;margin:0;padding:0}
  html,body{width:900px;height:1200px;overflow:hidden;background:var(--frame)}
  .flyer{position:absolute;left:14px;top:14px;width:872px;height:1172px;background:var(--white);overflow:hidden;font-family:"Open Sans",Arial,sans-serif;color:var(--ink)}

  .portrait{position:absolute;left:0;top:0;width:500px;height:1172px;
    background:
      radial-gradient(ellipse 300px 560px at 330px 760px, rgba(17,17,17,1) 0%, rgba(17,17,17,.95) 55%, rgba(17,17,17,0) 100%),
      radial-gradient(ellipse 170px 330px at 110px 260px, rgba(255,255,255,.9) 0%, rgba(255,255,255,0) 100%),
      linear-gradient(180deg, var(--photo-light) 0%, var(--photo-pale) 38%, var(--photo-mid) 62%, var(--photo-dark) 80%, var(--photo-dark) 100%)}

  .curve{position:absolute;left:0;top:0}
  .recruiting{position:absolute;left:362px;top:585px;width:640px;margin-left:-320px;margin-top:-34px;text-align:center;
    transform:rotate(-90deg);font-family:"Oswald",Arial,sans-serif;font-weight:300;font-size:64px;letter-spacing:1px;color:var(--black);line-height:68px}

  .right{position:absolute;left:486px;top:0;width:386px;height:1172px;text-align:center}
  .hashtag{position:absolute;left:0;width:386px;top:100px;font-family:"Oswald",Arial,sans-serif;font-weight:400;font-size:38px;line-height:46px;color:var(--red);letter-spacing:.5px}
  .brand{position:absolute;left:43px;top:230px;width:300px;height:240px;display:flex;align-items:center;justify-content:center;gap:12px;
    font-family:"Oswald",Arial,sans-serif;font-weight:400;font-size:32px;color:var(--red)}
  .brand-dot{width:14px;height:14px;border-radius:50%;background:var(--red);flex:none}
  .slogan{position:absolute;left:0;width:386px;top:510px;font-family:"Oswald",Arial,sans-serif;font-weight:400;font-size:34px;line-height:1.18;color:var(--ink)}

  .question{position:absolute;left:0;width:386px;font-family:"Open Sans",Arial,sans-serif;font-weight:700;font-size:15px;color:var(--ink)}
  .q-income{top:622px}
  .q-facing{top:816px}
  .options{position:absolute;left:20px;width:346px;display:flex;justify-content:space-between}
  .options-income{top:658px}
  .options-facing{top:852px}
  .option{width:110px;display:flex;flex-direction:column;align-items:center}
  .option-icon{width:66px;height:66px;display:flex;align-items:center;justify-content:center}
  .option-label{margin-top:8px;font-weight:700;font-size:11px;color:var(--red);line-height:1.25;height:28px;display:flex;align-items:center}
  .tick-box{margin-top:4px;width:13px;height:13px;border:1.5px solid var(--grey);border-radius:50%}
  .no-job{font-family:"Oswald",Arial,sans-serif;font-weight:600;font-size:26px;line-height:.95;color:var(--red)}
  .figure-fill{width:34px;height:56px;border-radius:50%;background:radial-gradient(circle at 50% 40%, #f05a60, var(--red))}

  .contact{position:absolute;left:0;width:386px;top:1032px}
  .contact-title{font-family:"Oswald",Arial,sans-serif;font-weight:500;font-size:24px;color:var(--ink);line-height:1}
  .contact-name{margin-top:8px;font-family:"Oswald",Arial,sans-serif;font-weight:300;font-size:36px;letter-spacing:2px;color:var(--red);line-height:1}
  .strapline{margin-top:10px;font-family:"Open Sans",Arial,sans-serif;font-size:17px;color:var(--ink)}

  .details{position:absolute;left:34px;top:962px;color:var(--white)}
  .detail{display:flex;align-items:center;gap:10px;font-size:16px;font-weight:600;height:32px}
  .detail-phone{font-family:"Open Sans",Arial,sans-serif;font-weight:700;font-size:36px;height:56px;gap:14px}
  .social-mark{width:16px;height:16px;background:var(--white);flex:none}
</style>
</head>
<body>
<div class="flyer">
  <div class="portrait" role="img" aria-label="Photograph of the founder in a black top with white-blonde hair, left half of face shown against a pale background"></div>

  <svg class="curve" width="872" height="1172" viewBox="0 0 872 1172" aria-hidden="true">
    <defs>
      <linearGradient id="fold" x1="0" x2="1" y1="0" y2="0">
        <stop offset="0" stop-color="#bdbdbd" stop-opacity="0"/>
        <stop offset=".6" stop-color="#bdbdbd" stop-opacity=".9"/>
        <stop offset="1" stop-color="#ffffff" stop-opacity="0"/>
      </linearGradient>
      <linearGradient id="foldY" x1="0" x2="0" y1="0" y2="1">
        <stop offset="0" stop-color="#fff" stop-opacity="0"/>
        <stop offset=".5" stop-color="#fff" stop-opacity="1"/>
        <stop offset="1" stop-color="#fff" stop-opacity="0"/>
      </linearGradient>
      <mask id="foldMask"><rect x="260" y="400" width="60" height="380" fill="url(#foldY)"/></mask>
    </defs>
    <circle cx="636" cy="586" r="370" fill="#ffffff"/>
    <rect x="272" y="400" width="26" height="380" fill="url(#fold)" mask="url(#foldMask)"/>
    <path d="M432 560 L454 586 L432 612" fill="none" stroke="#9a9a9a" stroke-width="9" stroke-linecap="round" stroke-linejoin="round"/>
  </svg>

  <div class="recruiting">RECRUITING NOW!</div>

  <section class="right">
    <h1 class="hashtag">#BRIGHTSTEPPATH</h1>
    <div class="brand"><span class="brand-dot"></span>Bright Step Path</div>
    <p class="slogan">START TODAY<br>START EARNING!</p>

    <p class="question q-income">WOULD YOU LIKE AN EXTRA INCOME FOR...</p>
    <div class="options options-income">
      <div class="option">
        <div class="option-icon">
          <svg width="60" height="56" viewBox="0 0 60 56" aria-hidden="true">
            <path d="M6 26 A24 20 0 0 1 54 26 Q48 21 42 26 Q36 21 30 26 Q24 21 18 26 Q12 21 6 26Z" fill="#ec1f27"/>
            <path d="M30 26 L30 48" stroke="#ec1f27" stroke-width="3"/>
            <path d="M8 50 Q30 42 52 50" fill="none" stroke="#ec1f27" stroke-width="3" stroke-linecap="round"/>
          </svg>
        </div>
        <span class="option-label">A HOLIDAY?</span><span class="tick-box"></span>
      </div>
      <div class="option">
        <div class="option-icon">
          <svg width="60" height="40" viewBox="0 0 60 40" aria-hidden="true">
            <path d="M4 28 L4 20 Q4 17 8 16 L14 15 L21 6 Q23 4 26 4 L40 4 Q43 4 45 6 L52 15 Q56 16 56 20 L56 28Z" fill="#ec1f27"/>
            <path d="M23 14 L27 8 L34 8 L34 14Z M38 8 L42 8 L47 14 L38 14Z" fill="#fff"/>
            <circle cx="16" cy="30" r="6" fill="#ec1f27" stroke="#fff" stroke-width="2"/>
            <circle cx="44" cy="30" r="6" fill="#ec1f27" stroke="#fff" stroke-width="2"/>
          </svg>
        </div>
        <span class="option-label">A NEW CAR?</span><span class="tick-box"></span>
      </div>
      <div class="option">
        <div class="option-icon">
          <svg width="56" height="56" viewBox="0 0 56 56" aria-hidden="true">
            <g fill="none" stroke="#ec1f27" stroke-width="5" stroke-linecap="round">
              <path d="M28 8 A20 20 0 0 1 46 22"/>
              <path d="M44 38 A20 20 0 0 1 20 46"/>
              <path d="M10 36 A20 20 0 0 1 14 14"/>
            </g>
            <g fill="#ec1f27">
              <path d="M40 22 L50 26 L50 15Z"/>
              <path d="M22 40 L14 47 L24 51Z"/>
              <path d="M8 18 L18 12 L10 8Z"/>
            </g>
          </svg>
        </div>
        <span class="option-label">LIFESTYLE CHANGES?</span><span class="tick-box"></span>
      </div>
    </div>

    <p class="question q-facing">ARE YOU FACING...</p>
    <div class="options options-facing">
      <div class="option">
        <div class="option-icon"><span class="no-job">NO<br>JOB</span></div>
        <span class="option-label">REDUNDANCY?</span><span class="tick-box"></span>
      </div>
      <div class="option">
        <div class="option-icon"><div class="figure-fill" role="img" aria-label="Icon of an expecting mother"></div></div>
        <span class="option-label">BIRTH OF A NEW CHILD?</span><span class="tick-box"></span>
      </div>
      <div class="option">
        <div class="option-icon">
          <svg width="54" height="54" viewBox="0 0 54 54" aria-hidden="true">
            <rect x="8" y="4" width="34" height="44" fill="#fff" stroke="#ec1f27" stroke-width="3"/>
            <rect x="14" y="10" width="22" height="6" fill="#ec1f27"/>
            <path d="M14 24 H36 M14 30 H36 M14 36 H28" stroke="#ec1f27" stroke-width="3"/>
            <circle cx="42" cy="42" r="9" fill="#ec1f27"/>
            <path d="M42 37 V47 M38 42 H46" stroke="#fff" stroke-width="2.5"/>
          </svg>
        </div>
        <span class="option-label">HEFTY BILLS?</span><span class="tick-box"></span>
      </div>
    </div>

    <div class="contact">
      <p class="contact-title">CONTACT</p>
      <p class="contact-name">YVONNE DARCOTT</p>
      <p class="strapline">Empowering others to achieve</p>
    </div>
  </section>

  <div class="details">
    <div class="detail detail-phone">
      <svg width="30" height="34" viewBox="0 0 24 24" aria-hidden="true"><path fill="#fff" d="M6.6 10.8a15.2 15.2 0 0 0 6.6 6.6l2.2-2.2a1 1 0 0 1 1-.25 11.4 11.4 0 0 0 3.6.57 1 1 0 0 1 1 1V20a1 1 0 0 1-1 1A17 17 0 0 1 3 4a1 1 0 0 1 1-1h3.5a1 1 0 0 1 1 1c0 1.25.2 2.45.57 3.6a1 1 0 0 1-.25 1z"/></svg>
      <span>07419 604172</span>
    </div>
    <div class="detail">
      <svg width="18" height="14" viewBox="0 0 18 14" aria-hidden="true"><rect x="1" y="1" width="16" height="12" fill="none" stroke="#fff" stroke-width="1.6"/><path d="M1 1 L9 8 L17 1" fill="none" stroke="#fff" stroke-width="1.6"/></svg>
      <span>Yvonne@brightsteppath-example.co.uk</span>
    </div>
    <div class="detail"><span class="social-mark"></span><span>@Bright_StepPath</span></div>
    <div class="detail"><span class="social-mark"></span><span>yvonbrightsteppath</span></div>
  </div>
</div>
</body>
</html>
```